Year 12 Chemistry Workbook illustrations and diagrams

We are producing a Chemistry Workbook for senior high-school students in South Australia and require a designer to create illustrations including detailed diagrams and graphs for our upcoming publication.

The attached files are illustrations that we'd like to have recreated, with your own personal style incorporated.

We will require you to do the following:
- Create vector artwork
- Supply AI files
- Use the font helvetica neue 45 light, or its italic variation
- Use full colour wherever possible
- Please use 100% black, not RGB black/eye-dropped black

Target Market(s)

Senior high school students

Industry/Entity Type

School

Font styles to use
Sans Serif

Colors

Designer to choose colors to be used in the design.

Requirements
Must have
• - Create vector artwork
• - Supply AI files
• - Use the font helvetica neue 45 light, or its italic variation
• - Use full colour wherever possible
• - Please use 100% black, not RGB black/eye-dropped black
Should not have
• Please do not use RGB black/eye-dropped black

```html
<!DOCTYPE html>
<html lang="en">
<head>
<meta charset="UTF-8">
<title>Oil accumulation process in an oleaginous microorganism</title>
<link rel="stylesheet" href="https://fonts.googleapis.com/css2?family=Inter:wght@300;400;700&display=swap">
<style>
  :root {
    --ink: #000000;
    --page: #ffffff;
    --panel: #0066b3;
    --heading: #fff200;
    --axis: #ffffff;
    --curve: #d7191f;
    --plot-top: #d8effb;
    --plot-bottom: #8dcdf1;
  }
  html, body {
    margin: 0;
    padding: 0;
    width: 1200px;
    height: 912px;
    overflow: hidden;
    background: var(--page);
  }
  .figure {
    display: block;
    width: 1200px;
    height: 912px;
    font-family: "Inter", "Helvetica Neue", Arial, sans-serif;
    font-weight: 300;
  }
  .intro, .caption { fill: var(--ink); }
  .intro { font-size: 40px; }
  .caption { font-size: 24px; }
  .panel { fill: var(--panel); }
  .heading { fill: var(--heading); font-size: 45px; font-weight: 700; }
  .axis-line, .tick { stroke: var(--axis); stroke-width: 3; fill: none; }
  .divider { stroke: var(--axis); stroke-width: 5; }
  .arrow { stroke: var(--axis); stroke-width: 3; fill: none; }
  .arrow-head { fill: var(--axis); }
  .tick-label, .phase-label, .axis-title { fill: var(--axis); font-size: 24px; }
  .axis-title { font-size: 26px; }
  .curve { stroke: var(--curve); stroke-width: 2; fill: none; }
</style>
</head>
<body>
<svg class="figure" viewBox="0 0 1500 1140" xmlns="http://www.w3.org/2000/svg">
  <defs>
    <linearGradient id="plot-fill" x1="0" y1="0" x2="0" y2="1">
      <stop offset="0" stop-color="var(--plot-top)"/>
      <stop offset="1" stop-color="var(--plot-bottom)"/>
    </linearGradient>
  </defs>

  <text class="intro" x="750" y="74" text-anchor="middle">The following graph represents the relative changes in glucose,</text>
  <text class="intro" x="750" y="122" text-anchor="middle">lipids (oils), and biomass for algae during their growth.</text>

  <rect class="panel" x="150" y="148" width="1200" height="898" rx="30"/>

  <text class="heading" x="740" y="238" text-anchor="middle">Oil accumulation process in an</text>
  <text class="heading" x="740" y="295" text-anchor="middle">oleaginous microorganism</text>

  <g class="phases">
    <line class="divider" x1="629" y1="324" x2="629" y2="387"/>
    <line class="arrow" x1="418" y1="358" x2="446" y2="358"/>
    <polygon class="arrow-head" points="405,358 420,351 420,365"/>
    <text class="phase-label" x="502" y="349" text-anchor="middle">balance</text>
    <text class="phase-label" x="502" y="376" text-anchor="middle">growth</text>
    <line class="arrow" x1="555" y1="358" x2="612" y2="358"/>
    <polygon class="arrow-head" points="624,358 609,351 609,365"/>
    <line class="arrow" x1="646" y1="358" x2="758" y2="358"/>
    <polygon class="arrow-head" points="634,358 649,351 649,365"/>
    <text class="phase-label" x="880" y="366" text-anchor="middle">lipid accumulation</text>
    <line class="arrow" x1="1000" y1="358" x2="1100" y2="358"/>
    <polygon class="arrow-head" points="1112,358 1097,351 1097,365"/>
  </g>

  <rect x="407" y="388" width="705" height="500" fill="url(#plot-fill)"/>
  <path class="axis-line" d="M407,388 V888 H1112 V388"/>

  <g class="left-axis">
    <path class="tick" d="M383,388H407M383,513H407M383,638H407M383,763H407M383,888H407"/>
    <text class="tick-label" x="370" y="397" text-anchor="end">100</text>
    <text class="tick-label" x="370" y="522" text-anchor="end">75</text>
    <text class="tick-label" x="370" y="647" text-anchor="end">50</text>
    <text class="tick-label" x="370" y="772" text-anchor="end">25</text>
    <text class="tick-label" x="370" y="897" text-anchor="end">0</text>
    <text class="axis-title" transform="translate(270 645) rotate(-90)" text-anchor="middle">Glucose/Nitrogen</text>
    <text class="axis-title" transform="translate(306 645) rotate(-90)" text-anchor="middle">(arbitrary values)</text>
  </g>

  <g class="bottom-axis">
    <path class="tick" d="M407,888V912M583,888V912M759,888V912M935,888V912M1112,888V912"/>
    <text class="tick-label" x="407" y="944" text-anchor="middle">0</text>
    <text class="tick-label" x="583" y="944" text-anchor="middle">25</text>
    <text class="tick-label" x="759" y="944" text-anchor="middle">50</text>
    <text class="tick-label" x="935" y="946" text-anchor="middle">75</text>
    <text class="tick-label" x="1112" y="944" text-anchor="middle">100</text>
    <text class="axis-title" x="759" y="984" text-anchor="middle">Time (arbitrary scale)</text>
  </g>

  <g class="right-axis">
    <path class="tick" d="M1112,418H1140M1112,575H1140M1112,730H1140M1112,888H1140"/>
    <text class="tick-label" x="1150" y="427">60</text>
    <text class="tick-label" x="1150" y="584">40</text>
    <text class="tick-label" x="1150" y="739">20</text>
    <text class="tick-label" x="1150" y="897">0</text>
    <text class="axis-title" transform="translate(1218 645) rotate(-90)" text-anchor="middle">Biomass (dry wt)</text>
    <text class="axis-title" transform="translate(1254 645) rotate(-90)" text-anchor="middle">Lipid (% dry wt)</text>
  </g>

  <g class="curves">
    <path class="curve nitrogen" d="M407,388 C520,410 570,560 595,720 C608,800 618,850 628,888"/>
    <path class="curve glucose" d="M407,388 C550,440 700,560 800,640 C900,720 1000,800 1112,858"/>
    <path class="curve biomass" d="M407,858 C470,860 490,840 520,800 C600,690 700,540 820,470 C920,420 1050,418 1112,418"/>
    <path class="curve lipid" d="M407,822 C550,824 650,820 700,815 C780,808 850,740 920,660 C980,590 1010,530 1050,490 C1070,475 1090,478 1112,478"/>
  </g>

  <text class="caption" x="750" y="1090" text-anchor="middle">(Simplify, relative percentages of biomass, lipid (oil), glucose over time.)</text>
</svg>
</body>
</html>
```